Tarvelo House

I am looking at a A4 one sided fact sheet about the property I developed, which I can print off or send electronically
Our current logo is Navy blue and Maroon colors
Industry/Entity Type
House

```html
<!DOCTYPE html>
<html lang="en">
<head>
<meta charset="utf-8">
<title>Tarvelo House – Property Fact Sheet</title>
<link rel="stylesheet" href="https://fonts.googleapis.com/css2?family=Cabin:wght@400;500&family=Roboto:wght@700&display=swap">
<style>
  :root {
    --navy: #1e2a5a;
    --maroon: #7f232a;
    --panel-grey: #f2f2f2;
    --slate: #6c6d93;
    --plum: #5e3f63;
    --ink: #3b3b3b;
    --muted: #6a6a6a;
    --white: #ffffff;
    --page-bg: #e9e9ec;
  }
  * { box-sizing: border-box; margin: 0; padding: 0; }
  html, body { width: 952px; height: 1200px; overflow: hidden; background: var(--page-bg); }
  body { font-family: "Cabin", sans-serif; position: relative; }

  .sheet {
    position: absolute; left: 52px; top: 0;
    width: 825px; height: 1167px;
    background: var(--white);
    transform: scale(1.028); transform-origin: 0 0;
    overflow: hidden;
  }
  .hero-photo {
    position: absolute; left: 30px; top: 60px; width: 766px; height: 441px;
    background: linear-gradient(180deg, #5b8fd1 0%, #a9c7e6 35%, #c9cdd1 55%, #7b8a7a 80%, #55585c 100%);
  }
  .shapes { position: absolute; left: 0; top: 0; width: 825px; height: 1167px; pointer-events: none; }

  .brand {
    position: absolute; left: 32px; top: 42px;
    display: flex; align-items: center; gap: 12px;
    color: var(--white); font-family: "Cabin", sans-serif; font-weight: 500;
    font-size: 30px; line-height: 34px;
  }
  .brand-mark { width: 18px; height: 18px; background: var(--white); }

  .facts {
    position: absolute; left: 30px; top: 520px; width: 766px; height: 226px;
    background: var(--panel-grey);
    display: grid; grid-template-columns: 254px 255px 257px; grid-template-rows: 116px 110px;
  }
  .fact {
    display: flex; flex-direction: column; align-items: center; justify-content: flex-start;
    padding-top: 18px; text-align: center; color: var(--ink);
  }
  .fact:nth-child(-n+3) { border-bottom: 1px dotted #b9b9b9; }
  .fact:not(:nth-child(3n)) { border-right: 1px dotted #b9b9b9; }
  .fact-icon { width: 40px; height: 42px; fill: var(--plum); margin-bottom: 4px; }
  .fact-label { font-size: 13px; line-height: 16px; }
  .fact-value { font-size: 12.5px; line-height: 16px; color: var(--muted); }

  .strategy {
    position: absolute; left: 30px; top: 762px; width: 766px; height: 304px;
    background: var(--slate);
  }
  .gallery-main, .gallery-thumb { position: absolute; border: 2px solid #9fa0bb; }
  .gallery-main { left: 10px; top: 20px; width: 378px; height: 127px;
    background: linear-gradient(180deg, #d9d3c6 0%, #b7aa94 55%, #3a3a3c 100%); }
  .thumb-office { left: 10px; top: 153px; width: 122px; height: 129px;
    background: linear-gradient(180deg, #e6e6e2 0%, #c8c0a8 60%, #a7b08a 100%); }
  .thumb-gym { left: 138px; top: 153px; width: 123px; height: 129px;
    background: linear-gradient(160deg, #e0873a 0%, #8a9b5a 45%, #4b4f58 100%); }
  .thumb-lounge { left: 267px; top: 153px; width: 121px; height: 129px;
    background: linear-gradient(180deg, #f2f1ee 0%, #dcd8d0 70%, #bfb8ac 100%); }

  .strategy-title {
    position: absolute; left: 403px; top: 16px; width: 245px;
    color: var(--white); font-size: 24px; font-weight: 400;
    padding-bottom: 7px; border-bottom: 1px solid var(--white);
  }
  .strategy-body {
    position: absolute; left: 403px; top: 68px; width: 353px;
    color: var(--white); font-size: 12.4px; line-height: 15.3px; letter-spacing: 0.35px;
    text-align: justify;
  }

  .contact {
    position: absolute; left: 30px; top: 1070px; color: var(--white); list-style: none;
    font-size: 10px; line-height: 18px;
  }
  .contact li { display: flex; align-items: center; gap: 6px; }
  .contact svg { width: 9px; height: 9px; fill: var(--white); }
  .contact .web { font-family: "Roboto", sans-serif; font-weight: 700; font-size: 13px; margin-top: 3px; }
</style>
</head>
<body>
<main class="sheet">
  <div class="hero-photo" role="img" aria-label="Photograph of the six-storey glass and aluminium office building on a street corner with parked cars and trees"></div>

  <svg class="shapes" viewBox="0 0 825 1167" aria-hidden="true">
    <polygon points="0,0 520,0 612,62 0,238" fill="var(--navy)"/>
    <line x1="0" y1="238" x2="612" y2="62" stroke="var(--white)" stroke-width="3"/>
    <polygon points="520,0 825,0 825,186" fill="var(--maroon)"/>
    <line x1="515" y1="-3" x2="828" y2="188" stroke="var(--white)" stroke-width="4"/>
  </svg>

  <div class="brand">
    <span class="brand-mark"></span>
    <span class="brand-name">Crestline Developments</span>
  </div>

  <section class="facts">
    <div class="fact">
      <svg class="fact-icon" viewBox="0 0 40 42"><circle cx="17" cy="6" r="5"/><rect x="16" y="10" width="2" height="14"/><polygon points="2,26 38,22 38,40 2,40"/></svg>
      <span class="fact-label">Address</span>
      <span class="fact-value">27 Arden Road South Brisbane</span>
    </div>
    <div class="fact">
      <svg class="fact-icon" viewBox="0 0 40 42"><polygon points="4,16 18,12 18,40 4,40"/><polygon points="20,6 34,2 34,40 20,40"/></svg>
      <span class="fact-label">Developed</span>
      <span class="fact-value">2008</span>
    </div>
    <div class="fact">
      <svg class="fact-icon" viewBox="0 0 40 42"><rect x="2" y="28" width="6" height="12"/><rect x="11" y="22" width="6" height="18"/><rect x="20" y="16" width="6" height="24"/><rect x="29" y="10" width="6" height="30"/><polyline points="2,22 14,12 22,16 36,4" fill="none" stroke="var(--plum)" stroke-width="3"/><polygon points="30,2 38,2 38,10"/></svg>
      <span class="fact-label">Value on Completion $87m</span>
      <span class="fact-value">Size: 5,700m2 NLA</span>
    </div>
    <div class="fact">
      <svg class="fact-icon" viewBox="0 0 40 42"><circle cx="16" cy="16" r="10" fill="none" stroke="var(--plum)" stroke-width="5"/><rect x="23" y="26" width="14" height="6" transform="rotate(45 23 26)"/></svg>
      <span class="fact-label">Type of Property</span>
      <span class="fact-value">A Grade Commercial Office Space</span>
    </div>
    <div class="fact">
      <svg class="fact-icon" viewBox="0 0 40 42"><ellipse cx="24" cy="14" rx="14" ry="10"/><ellipse cx="15" cy="24" rx="13" ry="10"/><polygon points="6,30 4,40 14,32"/></svg>
      <span class="fact-label">Quality rating</span>
      <span class="fact-value">4 Star</span>
    </div>
    <div class="fact">
      <svg class="fact-icon" viewBox="0 0 40 42"><circle cx="20" cy="7" r="6"/><rect x="17" y="12" width="6" height="14"/><rect x="8" y="26" width="24" height="7" rx="2"/><rect x="8" y="36" width="24" height="3"/></svg>
      <span class="fact-label">Developed by</span>
      <span class="fact-value">Crestline Development Corporation Pty Ltd</span>
    </div>
  </section>

  <section class="strategy">
    <div class="gallery-main" role="img" aria-label="Photograph of a boardroom with a long timber table and black leather chairs"></div>
    <div class="gallery-thumb thumb-office" role="img" aria-label="Photograph of an open-plan office and breakout area"></div>
    <div class="gallery-thumb thumb-gym" role="img" aria-label="Photograph of the staff gym with exercise equipment"></div>
    <div class="gallery-thumb thumb-lounge" role="img" aria-label="Photograph of a white lounge area with a reclining chair"></div>

    <h2 class="strategy-title">Development Strategy</h2>
    <p class="strategy-body">Tarvelo is a world class mining engineering firm. They had 6 offices spread out of a number of locations in the Southern part of Brisbane. Working with Tarvelo, we identified a site for their new headquarters. We purchased the land and applied for a development approval to develop a 15,700m2 office building on the site. We designed an office building around their requirements including their staff requirements, gym, bike rack, change rooms, outdoor dining areas, café, large car parking facility, storage etc. We appointed Marlow Builders to undertake a “design and construct” contract to build the development. Construction lasted about 18 months and we completed an integrated fitout to get them into the office space quicker. The property was sold on completion to American based fund manager Hollis for $87.2m</p>
  </section>

  <svg class="shapes" viewBox="0 0 825 1167" aria-hidden="true">
    <polygon points="0,997 512,1099 825,1167 0,1167" fill="var(--navy)"/>
    <line x1="-2" y1="996" x2="512" y2="1099" stroke="var(--white)" stroke-width="3"/>
    <polygon points="512,1099 825,1066 825,1162" fill="var(--maroon)"/>
    <line x1="512" y1="1099" x2="828" y2="1065" stroke="var(--white)" stroke-width="3"/>
  </svg>

  <ul class="contact">
    <li><svg viewBox="0 0 10 10"><path d="M2 0 L4 2 L3 4 Q4 6 6 7 L8 6 L10 8 L8 10 Q1 9 0 2 Z"/></svg>0400 555 218</li>
    <li><svg viewBox="0 0 10 10"><path d="M0 2 H10 V9 H0 Z M0 2 L5 6 L10 2" fill="none" stroke="#fff" stroke-width="1.4"/></svg>info@crestlinedev.com.au</li>
    <li><svg viewBox="0 0 10 10"><polygon points="5,0 10,5 8.5,5 8.5,10 6,10 6,7 4,7 4,10 1.5,10 1.5,5 0,5"/></svg>Level 1 | 15 Harbour Street GPO Box 1200 Brisbane QLD 4000</li>
    <li class="web">www.crestlinedev.com.au</li>
  </ul>
</main>
</body>
</html>
```